TalkHarbor - Language Coaching Services

Sleek, innovative, trendy design for Language Coaching business.

TalkHarbor is a new UK based company that provides Language Coaching services. We offer highly personalized on-line and face to face language courses. We also impart learning techniques workshops based on the latest neuroscience research for second-language acquisition.

Target Market(s)

See attached info

Industry/Entity Type

Consulting

Contact Information for Business Card

TalkHarbor
DaniaKV@talkharbor.co.uk
TalkHarbor.co.uk
London, UK

Font styles to use
Sans Serif

```html
<!DOCTYPE html>
<html lang="en">
<head>
<meta charset="utf-8">
<title>TalkHarbor – Business Card</title>
<link rel="stylesheet" href="https://fonts.googleapis.com/css2?family=Open+Sans:wght@400;600;700&display=swap">
<style>
  :root {
    --backdrop: #3a3a3b;
    --card: #242323;
    --card-edge: #1b1a1a;
    --brand-blue: #1e8fc9;
    --silver: #8d8d8f;
    --text-light: #f2f2f2;
    --divider: #e6e6e6;
  }
  * { box-sizing: border-box; margin: 0; padding: 0; }
  html, body {
    width: 1200px; height: 900px; overflow: hidden;
    background: var(--backdrop);
    font-family: "Open Sans", Arial, sans-serif;
  }
  .canvas {
    position: relative; width: 1200px; height: 900px;
  }
  .card {
    position: absolute; left: 240px; width: 720px; height: 400px;
    background: var(--card);
    border: 1px solid var(--card-edge);
    box-shadow: 0 14px 30px rgba(0,0,0,.45);
  }
  .card--front { top: 30px; }
  .card--back { top: 465px; }

  /* Front */
  .front-brand {
    position: absolute; left: 0; right: 0; top: 70px;
    display: flex; flex-direction: column; align-items: center;
  }
  .brand-circle {
    width: 118px; height: 118px; border-radius: 50%;
    border: 7px solid var(--silver);
  }
  .front-name {
    margin-top: 14px;
    font-size: 46px; font-weight: 600; letter-spacing: 1px;
    color: var(--silver);
  }
  .front-web {
    margin-top: 8px;
    font-size: 19px; font-weight: 600; letter-spacing: .5px;
    color: var(--brand-blue);
  }

  /* Back */
  .back-brand {
    position: absolute; left: 40px; top: 70px; width: 300px;
    display: flex; flex-direction: column; align-items: center;
  }
  .back-brand .brand-circle {
    width: 112px; height: 112px; border-color: var(--brand-blue);
  }
  .back-name {
    margin-top: 14px;
    font-size: 40px; font-weight: 600; letter-spacing: 1px;
    color: var(--brand-blue);
  }
  .divider {
    position: absolute; left: 362px; top: 60px;
    width: 2px; height: 160px; background: var(--divider);
  }
  .contact {
    position: absolute; left: 400px; top: 72px;
  }
  .contact-title {
    font-size: 22px; font-weight: 700; color: var(--brand-blue);
    margin-bottom: 10px;
  }
  .contact-list { list-style: none; }
  .contact-item {
    display: flex; align-items: center; gap: 14px;
    font-size: 18px; color: var(--text-light); letter-spacing: .4px;
    line-height: 32px;
  }
  .icon { width: 20px; height: 20px; flex: none; fill: var(--brand-blue); }
  .address {
    position: absolute; left: 120px; top: 300px;
    display: flex; align-items: center; gap: 14px;
    font-size: 19px; color: var(--text-light); letter-spacing: .4px;
  }
</style>
</head>
<body>
<main class="canvas">

  <section class="card card--front" aria-label="Card front">
    <div class="front-brand">
      <div class="brand-circle" aria-hidden="true"></div>
      <div class="front-name">TalkHarbor</div>
      <div class="front-web">www.talkharbor.co.uk</div>
    </div>
  </section>

  <section class="card card--back" aria-label="Card back">
    <div class="back-brand">
      <div class="brand-circle" aria-hidden="true"></div>
      <div class="back-name">TalkHarbor</div>
    </div>

    <div class="divider" aria-hidden="true"></div>

    <div class="contact">
      <p class="contact-title">TalkHarbor</p>
      <ul class="contact-list">
        <li class="contact-item">
          <svg class="icon" viewBox="0 0 24 24" aria-hidden="true"><path d="M6.6 10.8a15.1 15.1 0 0 0 6.6 6.6l2.2-2.2c.3-.3.7-.4 1-.2 1.1.4 2.3.6 3.6.6.6 0 1 .4 1 1V20c0 .6-.4 1-1 1A17 17 0 0 1 3 4c0-.6.4-1 1-1h3.5c.6 0 1 .4 1 1 0 1.3.2 2.5.6 3.6.1.3 0 .7-.2 1z"/></svg>
          <span>+44 1632 960218</span>
        </li>
        <li class="contact-item">
          <svg class="icon" viewBox="0 0 24 24" aria-hidden="true"><path d="M2 5h20v14H2z M3.5 6.5 12 13l8.5-6.5" stroke="#242323" stroke-width="1.5"/></svg>
          <span>daniakv@talkharbor.co.uk</span>
        </li>
        <li class="contact-item">
          <svg class="icon" viewBox="0 0 24 24" aria-hidden="true"><circle cx="12" cy="12" r="10"/><path d="M2 12h20M12 2c3 3 3 17 0 20M12 2c-3 3-3 17 0 20M4 7h16M4 17h16" stroke="#242323" stroke-width="1.3" fill="none"/></svg>
          <span>www.talkharbor.co.uk</span>
        </li>
      </ul>
    </div>

    <div class="address">
      <svg class="icon" viewBox="0 0 24 24" aria-hidden="true"><path d="M12 2a7 7 0 0 0-7 7c0 5 7 13 7 13s7-8 7-13a7 7 0 0 0-7-7zm0 9.5a2.5 2.5 0 1 1 0-5 2.5 2.5 0 0 1 0 5z"/></svg>
      <span>24 Harbour Lane, TN12 4QR, London, UK</span>
    </div>
  </section>

</main>
</body>
</html>
```